Boutique Real Estate Brokerage Tessly Realty Website Design

Winning designer work on migrate as well through nest ferry.
We need a new website as an informational hub to aid our print and digital strategy as well as showing that we are located in Brooklyn and Florida. I have a boutique real estate brokerage and advisory firm specializing in residential leasing, multifamily sales and 1031 Exchange appropriation. This won't be a portal to search properties, it will be a place for information. I'd like space for an ebook to be downloaded and information on my probate sales and multifamily leasing marketing campaigns. I included my logo and will leave it up to the designer to come up with colors to match it. I have also attached verbiage for each page. The final design should have a modern high end look that reflects gentrifying Brooklyn as well as beautiful Florida.
Thank you!
Target Market(s)
Owners of income producing real estate and develop-able land in Brooklyn, NY and Florida.
Industry/Entity Type
Real Estate
Coding
Coded - Design and coding required
Number of Pages Required
5+ page
Colors
Designer to choose colors to be used in the design.
Requirements
Must have
- A modern elegant look
Nice to have
- pictures of brooklyn and florida
Should not have
- real estate search pages

```html
<!DOCTYPE html>
<html lang="en">
<head>
<meta charset="utf-8">
<title>Tessly Realty NYC</title>
<link href="https://fonts.googleapis.com/css2?family=Russo+One&family=Poppins:wght@400;500;600&display=swap" rel="stylesheet">
<style>
:root{
  --black:#0d0d0d;
  --white:#ffffff;
  --grey-bg:#f3f3f3;
  --text:#222222;
  --muted:#555555;
  --green:#72b89b;
  --teal:#4fa58f;
}
*{margin:0;padding:0;box-sizing:border-box}
html,body{width:1200px;height:3789px;overflow:hidden}
body{font-family:"Poppins",sans-serif;color:var(--text);background:var(--white);position:relative}
.abs{position:absolute}
h1,h2,h3,.heading{font-family:"Russo One",sans-serif;font-weight:400}

/* header */
.topbar{left:0;top:0;width:1200px;height:111px;background:var(--black)}
.brand{left:92px;top:34px;display:flex;align-items:center;gap:18px;color:var(--white);font-family:"Russo One",sans-serif;font-size:22px;letter-spacing:2px}
.brand-mark{width:40px;height:40px;background:#8a8a8a;border-radius:4px}
.account{right:92px;top:44px;display:flex;gap:44px;color:var(--white);font-size:15px}
.account span{display:flex;align-items:center;gap:10px}
.nav{left:0;top:111px;width:1200px;height:63px;background:var(--white);display:flex;justify-content:center;align-items:center;gap:46px;font-size:16px;color:var(--text);border-bottom:1px solid #eee}

/* hero */
.hero{left:0;top:174px;width:1200px;height:559px;
  background:
    linear-gradient(180deg,rgba(0,0,0,.15) 0%,rgba(0,0,0,0) 40%,rgba(0,0,0,.25) 100%),
    radial-gradient(ellipse 320px 300px at 1130px 120px,#8fb9e0 0%,rgba(143,185,224,0) 70%),
    linear-gradient(100deg,#4a2e24 0%,#7a5040 14%,#5c3a2e 26%,#8a6450 38%,#5a4034 50%,#6c4c3c 62%,#4a3a2a 72%,#3e6a2a 82%,#5c9a3a 92%,#76b24a 100%)}
.hero-title{left:0;top:348px;width:1200px;text-align:center;color:var(--white);font-size:50px;line-height:63px;text-shadow:0 2px 6px rgba(0,0,0,.35)}
.btn-outline{border:2px solid var(--white);color:var(--white);display:flex;align-items:center;justify-content:center;border-radius:4px;font-size:20px}
.arrow{width:32px;height:32px;border-radius:50%;background:var(--white);display:flex;align-items:center;justify-content:center}

/* help */
.section-title{left:0;width:1200px;text-align:center;font-size:38px;color:var(--black)}
.card-img{top:887px;width:324px;height:224px;border-radius:4px;box-shadow:0 2px 6px rgba(0,0,0,.12)}
.card-label{top:1145px;width:324px;text-align:center;font-size:26px;line-height:31px;color:var(--text)}

/* story */
.story{left:0;top:1258px;width:1200px;height:465px;
  background:
    linear-gradient(180deg,rgba(0,0,0,.45),rgba(0,0,0,.55)),
    linear-gradient(90deg,#2a1e18 0%,#4a3428 15%,#2c2320 35%,#3a2c24 55%,#2a2420 70%,#5a3a2a 88%,#3a2a22 100%)}
.story p{left:190px;top:146px;width:833px;text-align:center;color:#e8e8e8;font-size:17.5px;line-height:37px}
.btn-green{background:var(--green);color:var(--white);display:flex;align-items:center;justify-content:center;border-radius:4px;font-size:19px}

/* mortgage */
.mortgage{left:0;top:1723px;width:1200px;height:614px;background:var(--grey-bg)}
.tabs{left:149px;top:242px;width:869px;height:63px;border:2px solid #b9b9b9;border-radius:6px;display:flex;justify-content:space-around;align-items:center;font-size:19px;color:var(--text);background:var(--white)}
.tab-active{position:relative}
.tab-active::after{content:"";position:absolute;left:10%;right:10%;bottom:-12px;height:4px;background:#444}
.field-label{font-size:17px;color:var(--text)}
.input{height:41px;background:var(--white);border:2px solid #c9c9c9;border-radius:5px;display:flex;align-items:center;justify-content:space-between;padding:0 10px;color:#aaa;font-size:17px}

/* ebook */
.ebook{left:0;top:2337px;width:1200px;height:384px;
  background:
    linear-gradient(90deg,rgba(0,0,0,.35),rgba(0,0,0,.1) 60%,rgba(0,0,0,.35)),
    linear-gradient(115deg,#1a1a1a 0%,#2e2e2e 30%,#1f1f1f 50%,#3a3a3a 72%,#1c1c1c 100%)}
.book{left:139px;top:25px;width:253px;height:316px;border-radius:3px;box-shadow:8px 10px 18px rgba(0,0,0,.55);
  background:
    linear-gradient(90deg,rgba(0,0,0,.3) 0%,rgba(0,0,0,0) 9%),
    linear-gradient(180deg,#e23a30 0%,#d12a24 40%,#c9a24a 58%,#b88a2e 66%,#d12a24 76%,#b51c1a 100%)}

/* contact */
.contact-left{left:0;top:2721px;width:652px;height:596px;background:linear-gradient(180deg,var(--white) 0%,var(--white) 31%,#f1f1f1 31%,#f1f1f1 100%)}
.contact-photo{left:652px;top:2721px;width:548px;height:596px;
  background:
    linear-gradient(180deg,rgba(0,0,0,0) 55%,rgba(60,40,20,.25) 100%),
    linear-gradient(90deg,#a45a1e 0%,#c9782e 22%,#b3927a 40%,#c8b8a2 52%,#8c8c88 66%,#b8b8b4 78%,#6a6a66 88%,#9a5a24 100%)}
.field{left:91px;width:493px;background:var(--white);border:1.5px solid #d8d8d8;border-radius:3px;font-size:14px;color:#9a9a9a;padding:12px 14px}

/* footer */
.footer{left:0;top:3317px;width:1200px;height:472px;
  background:
    linear-gradient(180deg,rgba(0,0,0,.55),rgba(0,0,0,.75)),
    linear-gradient(90deg,#4a3428 0%,#2e2420 30%,#3a2c24 60%,#4a3a2c 100%)}
.footer h3{position:absolute;font-size:26px;color:var(--white)}
.footer .copy{color:#e6e6e6;font-size:16px;line-height:27px}
.contact-row{display:flex;gap:16px;align-items:flex-start}
.social{width:22px;height:22px;background:var(--white);border-radius:3px}
</style>
</head>
<body>

<header class="abs topbar">
  <div class="abs brand"><span class="brand-mark"></span>TESSLY REALTY</div>
  <div class="abs account">
    <span><svg width="16" height="16" viewBox="0 0 16 16"><circle cx="8" cy="8" r="8" fill="#fff"/><circle cx="8" cy="6" r="3" fill="#0d0d0d"/></svg>Have an account?</span>
    <span><svg width="18" height="16" viewBox="0 0 18 16"><circle cx="7" cy="4" r="4" fill="#fff"/><path d="M0 16c0-5 3-7 7-7s7 2 7 7z" fill="#fff"/></svg>Sign in</span>
    <span><svg width="18" height="16" viewBox="0 0 18 16"><circle cx="7" cy="4" r="4" fill="#fff"/><path d="M0 16c0-5 3-7 7-7s7 2 7 7z" fill="#fff"/><path d="M15 3v6M12 6h6" stroke="#fff" stroke-width="2"/></svg>Create Account</span>
  </div>
</header>

<nav class="abs nav">
  <span>Home &#9662;</span><span>Multi-Family Sales</span><span>Multi-Family Leasing</span><span>1031 Exchange Appropriation</span><span>Distressed Sales</span><span>Contact</span>
</nav>

<section class="abs hero" role="img" aria-label="Photo of Brooklyn brownstone row houses with trees"></section>
<svg class="abs" style="left:0;top:680px" width="1200" height="60" viewBox="0 0 1200 60" preserveAspectRatio="none">
  <path d="M0 30 C300 0 500 45 750 30 C950 18 1100 5 1200 25 L1200 60 L0 60 Z" fill="#fff"/>
  <path d="M0 30 C300 0 500 45 750 30 C950 18 1100 5 1200 25" fill="none" stroke="#4fa58f" stroke-width="6"/>
</svg>
<h1 class="abs hero-title">Assisting landlords increase profits<br>while decreasing the stress</h1>
<div class="abs btn-outline" style="left:505px;top:505px;width:190px;height:56px">View More</div>
<div class="abs arrow" style="left:26px;top:434px"><svg width="14" height="14" viewBox="0 0 14 14"><path d="M9 2L4 7l5 5" stroke="#222" stroke-width="2.5" fill="none"/></svg></div>
<div class="abs arrow" style="left:1140px;top:434px"><svg width="14" height="14" viewBox="0 0 14 14"><path d="M5 2l5 5-5 5" stroke="#222" stroke-width="2.5" fill="none"/></svg></div>

<h2 class="abs section-title" style="top:788px">How we can help</h2>
<div class="abs card-img" style="left:91px;background:linear-gradient(180deg,#fafafa 0%,#eceae6 35%,#d8d2c8 65%,#b09a7a 82%,#8a7a66 100%)" role="img" aria-label="Photo of a bright leased apartment interior"></div>
<div class="abs card-img" style="left:440px;background:linear-gradient(180deg,rgba(0,0,0,.2),rgba(0,0,0,.3)),linear-gradient(100deg,#8a7a6a 0%,#6a5a4c 30%,#7c6c5e 55%,#5a4a40 80%,#8a7c70 100%)" role="img" aria-label="Photo of a multifamily brick building with fire escapes"></div>
<div class="abs" style="left:440px;top:887px;width:324px;height:224px;display:flex;align-items:center;justify-content:center;color:#fff;font-size:21px">View More</div>
<div class="abs card-img" style="left:786px;background:linear-gradient(180deg,#c8d4e0 0%,#a8b8c4 18%,#7a8c6a 32%,#6a7e52 55%,#8a8a6a 72%,#4a6038 100%)" role="img" aria-label="Aerial photo of Florida land for site selection"></div>
<div class="abs card-label" style="left:91px">Multi-Family<br>Leasing</div>
<div class="abs card-label" style="left:440px">Multi-Family<br>Sales</div>
<div class="abs card-label" style="left:786px">Site Selection<br>Advisory</div>

<section class="abs story" role="img" aria-label="Dim photo of a Brooklyn street at dusk">
  <h2 class="abs section-title" style="top:52px;color:#fff">Our Story</h2>
  <p class="abs">Tessly Realty NYC is a full service real estate brokerage firm located in Brooklyn, NY and West Palm Beach, FL We specializes in assisting landlords by increasing their profits while decreasing their stress. Our firm concentrates on multifamily sales and leasing; distressed sales and 1031 Exchange property appropriation. With more than 12 years of experience in Brooklyn, we've narrowed our scope to its Northern and Eastern neighborhoods</p>
  <div class="abs btn-green" style="left:371px;top:359px;width:200px;height:48px">Learn More</div>
  <div class="abs btn-outline" style="left:606px;top:359px;width:202px;height:48px;font-size:19px">Contact Us</div>
</section>

<section class="abs mortgage">
  <h2 class="abs section-title" style="top:70px">Mortgage Tools</h2>
  <p class="abs" style="left:0;top:150px;width:1200px;text-align:center;font-size:19px;line-height:37px;color:var(--muted)">Tessly Realty NYC specializes in assisting landlords by increasing their profits<br>while decreasing their stress</p>
  <div class="abs tabs"><span>Mortgage Rates</span><span class="tab-active">Mortgage Calculator</span><span>Coverage Areas</span></div>
  <h2 class="abs section-title" style="top:366px;font-size:32px">Mortgage Calculator</h2>
  <div class="abs field-label" style="left:172px;top:445px">Home Price</div>
  <div class="abs field-label" style="left:659px;top:445px">Down Payment</div>
  <div class="abs input" style="left:172px;top:487px;width:424px"><span>$</span><span style="color:#555;font-size:11px">&#9650;<br>&#9660;</span></div>
  <div class="abs input" style="left:659px;top:487px;width:177px;background:#eee"><span>$</span><span style="color:#555;font-size:11px">&#9650;<br>&#9660;</span></div>
  <div class="abs btn-green" style="left:877px;top:488px;width:174px;height:39px;font-size:17px">Continue</div>
</section>

<section class="abs ebook" role="img" aria-label="Dark photo of a city street behind the ebook">
  <div class="abs book" role="img" aria-label="Cover of the probate real estate sales ebook"></div>
  <h2 class="abs heading" style="left:518px;top:68px;font-size:25px;color:#fff">Ebook</h2>
  <p class="abs" style="left:518px;top:112px;width:560px;color:#e5e5e5;font-size:16.5px;line-height:30.5px">Lorem ipsum dolor sit amet, consectetur adipiscing elit. Curabitur vitae mi semper, sollicitudin tortor in, eleifend ante. Pellentesque in dui massa. Mauris quis urna purus. Sed vel metus a lacus interdum sodales. Etiam et tincidunt sem Proin scelerisque eleifend turpis,</p>
  <div class="abs btn-outline" style="left:518px;top:285px;width:260px;height:43px;font-size:18px">Download the PDF</div>
</section>

<section class="abs contact-left">
  <h2 class="abs heading" style="left:91px;top:35px;font-size:35px;color:var(--black)">Contact Us</h2>
  <div class="abs field" style="top:123px;height:48px">Name</div>
  <div class="abs field" style="top:197px;height:48px">Email</div>
  <div class="abs field" style="top:262px;height:48px">Phone No</div>
  <div class="abs field" style="top:330px;height:142px">Message</div>
  <div class="abs btn-green" style="left:91px;top:515px;width:199px;height:48px;font-size:19px">Submit</div>
</section>
<div class="abs contact-photo" role="img" aria-label="Photo of a kitchen with wood cabinets and a steel stove"></div>

<footer class="abs footer">
  <h3 style="left:91px;top:80px">About Us</h3>
  <h3 style="left:541px;top:80px">Quick Links</h3>
  <h3 style="left:851px;top:80px">Contact Us</h3>
  <p class="abs copy" style="left:91px;top:156px;width:400px">Tessly Realty NYC is a full service real estate brokerage firm located in Brooklyn, NY and West Palm Beach, FL We specializes in assisting landlords by increasing their profits</p>
  <div class="abs copy" style="left:541px;top:163px;line-height:32.5px">Home<br>Multi-Family Sales<br>Multi-Family Leasing<br>1031 Exchange<br>Appropriation<br>Distressed Sales<br>Contact</div>
  <div class="abs copy" style="left:851px;top:157px;display:flex;flex-direction:column;gap:5px">
    <div class="contact-row"><svg width="16" height="27" viewBox="0 0 16 16"><path d="M3 1l3 3-2 2c1 2 3 4 5 5l2-2 3 3-2 3C7 15 1 9 1 3z" fill="#fff"/></svg>555-014-2280</div>
    <div class="contact-row"><svg width="16" height="27" viewBox="0 0 16 16"><rect x="1" y="3" width="14" height="10" fill="#fff"/><path d="M1 3l7 6 7-6" stroke="#22201e" stroke-width="1.5" fill="none"/></svg>mara@tesslynycrealty.com</div>
    <div class="contact-row"><svg width="16" height="27" viewBox="0 0 16 16"><path d="M8 1a5 5 0 0 1 5 5c0 4-5 9-5 9S3 10 3 6a5 5 0 0 1 5-5z" fill="#fff"/><circle cx="8" cy="6" r="2" fill="#22201e"/></svg>742 Linden Ave, 3,<br>Brooklyn, New York 11200</div>
  </div>
  <div class="abs copy" style="left:91px;top:414px;font-size:17px">© 2019 Tessly Realty NYC &amp; Hearthview</div>
  <div class="abs" style="left:960px;top:416px;display:flex;gap:18px">
    <span class="social"></span><span class="social"></span><span class="social"></span><span class="social"></span>
  </div>
</footer>

</body>
</html>
```